Tech Website

1. Overview
Prism48, formally named LumoVista, is a pioneer in computer vision technology and machine learning. Based out of Santa Clara, California, Prism48 is at the forefront of the User Interface revolution; building technology architecture that grants devices with the aptitude to respond to emotional detection, gaze tracking, facial recognition, age and gender identification and gaming interaction. Winner of the Mobile Track at NOVA Founders Sprint 2012, Prism48 has developed the next generation of consumer behaviour analytics. Prism48 software solutions are scalable across various platforms including mobile phone, tablets, PC and SmartTV.
Updates

Good day, 

Please see the update to our brief - there is a PDF of the type of format and design we are looking for.  It shows each page - Landing, Technology, Product, Press and Company.

Thank you for your designs

Regards,

Target Market(s)

Target market - A mix of enterprise and consumer audiences, targeting the need for the technology in the living room space

Industry/Entity Type

Architecture

Requirements
Must have
• Design preferences - Easy to navigate, modern with sleek feel, trendy, tech saavy, using cube as a consistent element/theme. colours are not determined, but parrot green was one idea with 2 additional underlying colours. keys words like user interface revolution or sense recognition are good sources to draw inspiration.

Landing page will have a video - illustrating different uses of technology

Technical Specs - Landing page, 6 tabs/subpages, and each subpage may have 1 or 2 additional pages. Coding will be necessary, not that much at the beginning stages.

```html
<!DOCTYPE html>
<html lang="en">
<head>
<meta charset="utf-8">
<title>Prism48</title>
<link rel="stylesheet" href="https://fonts.googleapis.com/css2?family=Arimo:wght@400;700&family=Oswald:wght@400&family=Questrial&family=Ubuntu:wght@400;500&family=PT+Sans:wght@400;700&display=swap">
<style>
:root{
  --green:#8fd85e;
  --accent:#5fa332;
  --nav-pill:#3f8a22;
  --nav-text:#2c4a1c;
  --hero:#262626;
  --hero-dark:#1a1a1a;
  --ink:#222;
  --body:#1e1e1e;
  --rule:#d6d6d6;
  --feed:#9edcf6;
  --feed-line:#cfcfcf;
  --feed-name:#4a4a4a;
  --footer:#111;
  --footer-text:#cfcfcf;
  --footer-muted:#8a8a8a;
  --icon:#7d7d7d;
  --btn:#3f7fc6;
}
html,body{margin:0;padding:0;overflow:hidden;}
body{width:1200px;height:1080px;background:#fff;font-family:"Arimo",Arial,sans-serif;}
.page{position:relative;width:1200px;height:1080px;overflow:hidden;}

/* header */
.site-header{position:absolute;left:0;top:0;width:1200px;height:75px;background:linear-gradient(#9be46a,var(--green) 60%,#84cf55);border-bottom:1px solid #6aa847;}
.brand{position:absolute;left:186px;top:14px;font-family:"Oswald",sans-serif;font-size:36px;line-height:44px;color:#f4f8ee;letter-spacing:0.5px;}
.main-nav{position:absolute;left:651px;top:25px;display:flex;font-family:"Ubuntu",sans-serif;font-size:12.2px;line-height:27px;}
.main-nav a{color:var(--nav-text);text-decoration:none;padding:0 8px;}
.main-nav a.active{background:var(--nav-pill);color:#fff;border-radius:14px;padding:0 16px;}

/* hero */
.hero{position:absolute;left:0;top:76px;width:1200px;height:369px;background:radial-gradient(ellipse at 55% 20%,#3a3a3a,var(--hero) 45%,var(--hero-dark));}
.hero-title{position:absolute;left:194px;top:108px;margin:0;font-family:"Questrial",sans-serif;font-weight:400;font-size:29px;line-height:39px;color:#fff;width:370px;letter-spacing:0.6px;}
.btn-learn{position:absolute;left:194px;top:247px;width:105px;height:38px;border-radius:9px;background:linear-gradient(#6ea4dd,var(--btn));border:1px solid #2f6aaa;color:#fff;font-size:11px;line-height:38px;text-align:center;}
.slider-dots{position:absolute;left:198px;top:339px;display:flex;gap:2px;}
.slider-dots span{width:9px;height:9px;border-radius:50%;background:#050505;}
.slider-dots span.on{background:#5cb338;}
.hero-visual{position:absolute;left:607px;top:65px;width:406px;height:304px;border-radius:30px 30px 0 0;background:linear-gradient(160deg,#202020 0%,#3b3b3b 30%,#9fc2cc 55%,#c7dde2 100%);}

/* welcome */
.welcome-band{position:absolute;left:0;top:446px;width:1200px;height:130px;background:linear-gradient(#d9d9d9,#fff);}
.section-title{margin:0;font-family:"Ubuntu",sans-serif;font-weight:400;font-size:16px;line-height:20px;color:var(--ink);}
.section-title em{font-style:normal;color:var(--accent);}
.welcome-title{position:absolute;left:177px;top:476px;}
.welcome-text{position:absolute;left:177px;top:508px;width:518px;margin:0;font-size:10.6px;line-height:18.6px;color:var(--body);text-align:justify;}
.welcome-photo{position:absolute;left:715px;top:476px;width:305px;height:176px;border:1px solid #bbb;background:linear-gradient(100deg,#cfd2d6,#eceae6 50%,#c9a88b 85%,#b89677);}
.divider{position:absolute;left:177px;top:679px;width:845px;height:1px;background:var(--rule);}

/* columns */
.tech-title{position:absolute;left:177px;top:704px;}
.team-title{position:absolute;left:497px;top:704px;}
.video{position:absolute;left:177px;top:744px;width:278px;height:154px;border:1px solid #999;background:linear-gradient(130deg,#1d2730,#5d6a72 45%,#c9d3d8 70%,#7b8d98);}
.video-bar{position:absolute;left:4px;bottom:4px;right:4px;height:18px;background:rgba(10,10,10,.85);border-radius:3px;}
.video-bar .play{position:absolute;left:6px;top:5px;}
.video-bar .track{position:absolute;left:42px;top:7px;width:170px;height:4px;background:#555;border:1px solid #888;}
.video-bar .track i{display:block;width:48px;height:4px;background:#2a9be0;}
.video-bar .hd{position:absolute;right:10px;top:3px;font-size:8px;font-weight:700;color:#2a9be0;font-style:italic;}
.team-photo{position:absolute;left:497px;top:744px;width:278px;height:154px;border:1px solid #999;background:linear-gradient(#e8edf1,#c9d0d6 45%,#23262c 75%,#1a1c20);}
.col-text{position:absolute;top:908px;width:280px;margin:0;font-size:10.6px;line-height:15.2px;color:var(--body);text-align:justify;}

/* feed */
.feed{position:absolute;left:801px;top:712px;width:207px;height:260px;background:var(--feed);border-radius:4px;font-family:"PT Sans",sans-serif;}
.feed-head{position:absolute;left:7px;top:7px;font-size:7px;color:#345;line-height:10px;}
.feed-head b{display:block;font-weight:400;font-size:10.5px;color:#1a2a38;line-height:14px;}
.feed-list{position:absolute;left:3px;top:36px;width:196px;height:200px;background:#fff;overflow:hidden;}
.tweet{position:relative;padding:4px 12px 4px 32px;border-bottom:1px solid var(--feed-line);font-size:8px;line-height:9.4px;color:#555;}
.tweet .av{position:absolute;left:6px;top:6px;width:16px;height:16px;background:#c9b08a;}
.tweet b{color:var(--feed-name);}
.tweet .link{color:#333;font-weight:700;}
.tweet small{display:block;font-size:6.5px;color:#666;font-weight:700;}
.feed-scroll{position:absolute;right:0;top:0;width:9px;height:200px;background:#eef4f9;border-left:1px solid #ccd;}
.feed-scroll i{position:absolute;left:1px;top:12px;width:6px;height:32px;background:#c3d3e6;border-radius:2px;}
.feed-foot{position:absolute;left:8px;right:8px;bottom:6px;display:flex;justify-content:space-between;font-size:8px;font-weight:700;color:#1b2b3a;line-height:12px;}
.feed-foot .net{color:#fff;font-size:10px;}

/* footer */
.site-footer{position:absolute;left:0;top:997px;width:1200px;height:83px;background:var(--footer);}
.footer-nav{position:absolute;left:180px;top:22px;font-size:11.5px;color:var(--footer-text);}
.footer-nav a{color:var(--footer-text);text-decoration:none;}
.footer-nav span{margin:0 8px;}
.footer-legal{position:absolute;left:180px;top:45px;font-size:10.5px;color:var(--footer-muted);}
.connect{position:absolute;left:765px;top:33px;font-size:11.5px;color:var(--footer-text);}
.social{position:absolute;top:24px;width:30px;height:30px;border-radius:5px;background:var(--icon);color:#fff;font-size:7px;line-height:30px;text-align:center;font-family:"Arimo",sans-serif;}
</style>
</head>
<body>
<div class="page">

  <header class="site-header">
    <div class="brand">Prism48</div>
    <nav class="main-nav">
      <a class="active" href="#">HOME</a>
      <a href="#">ABOUT US</a>
      <a href="#">PRESS</a>
      <a href="#">TECHNOLOGY</a>
      <a href="#">CONTACT US</a>
    </nav>
  </header>

  <section class="hero">
    <h1 class="hero-title">Always mobile applications to levarage front facing camera.</h1>
    <div class="btn-learn">LEARN MORE</div>
    <div class="slider-dots"><span class="on"></span><span></span><span></span><span></span><span></span></div>
    <div class="hero-visual" role="img" aria-label="Two smartphones side by side showing a home screen of app icons"></div>
  </section>

  <div class="welcome-band"></div>
  <h2 class="section-title welcome-title">WELCOME TO OUR <em>PRISM48</em></h2>
  <p class="welcome-text">Nam quis libero felis, et convallis nisl. Nullam pharetra, risus at sollicitudin cursus, est urna varius nunc, sit amet congue mauris risus eget erat. Donec eu dolor nec ligula congue blandit. Aliquam vestibulum, nunc in malesuada tempor, eros felis aliquet tellus, a vulputate quam nisl ac metus. Lorem ipsum dolor sit amet, consectetur adipiscing elit. Donec ac tempus nibh. Fusce leo nulla, feugiat et posuere fermentum, cursus eget eros. Pellentesque elementum lacus viverra risus dignissim sit amet dictum nibh ultricies. Nulla facilisi. Ut facilisis, purus in pellentesque ultricies, orci lectus laoreet lectus, sagittis scelerisque nunc mauris et arcu. Nam nec egestas ante. Sed eros nulla, pharetra a pretium nec, volutpat non mauris. Vivamus vitae massa at mi facilisis pellentesque. Sed lacinia tortor vel ligula tempus dignissim quis non leo.</p>
  <div class="welcome-photo" role="img" aria-label="Group of business people in an office, a smiling woman in front"></div>
  <div class="divider"></div>

  <h2 class="section-title tech-title">USES OF <em>TECHNOLOGY</em></h2>
  <div class="video" role="img" aria-label="Video still of a hand touching a tablet screen">
    <div class="video-bar">
      <svg class="play" width="10" height="9" viewBox="0 0 10 9"><path d="M1 0 L9 4.5 L1 9 Z" fill="#fff"/></svg>
      <div class="track"><i></i></div>
      <div class="hd">HD</div>
    </div>
  </div>
  <p class="col-text" style="left:178px">Praesent rutrum tellus et augue pretium pellentesque sed eleifend massa. Donec eu felis risus. Suspendisse interdum justo vel purus tempor commodo. Morbi nec quam lorem. Morbi sed augue lectus.</p>

  <h2 class="section-title team-title">OUR <em>TEAM</em></h2>
  <div class="team-photo" role="img" aria-label="Team of five business people in suits"></div>
  <p class="col-text" style="left:498px">Suspendisse interdum justo vel purus tempor commodo. Morbi nec quam lorem. Morbi sed augue lectus. Fusce adipiscing, tortor a convallis accumsan, urna orci porttitor eros, vitae faucibus nisl diam non purus.</p>

  <aside class="feed">
    <div class="feed-head">Chirper feed<b>Prism 48</b></div>
    <div class="feed-list">
      <div class="tweet"><span class="av"></span><b>PreviewPress</b> 'The voice of the unheard' <span class="link">http://fw.io/HGdjc3Yw</span><small>43 minutes ago</small></div>
      <div class="tweet"><span class="av"></span><b>PreviewPress</b> Heart's destiny <span class="link">http://fw.io/J3cAgA2b</span><small>45 minutes ago</small></div>
      <div class="tweet"><span class="av" style="background:#3d5f9e"></span><b>DailyLedger</b> #Rovers top #Ashby; #Hartwell wins easily in the final <span class="link">http://sh.rt /bTIxc8</span><small>about 1 hour ago</small></div>
      <div class="tweet"><span class="av" style="background:#8a9a8a"></span><b>ivanmoreno</b> Local hero saves old library from burning - <span class="link">http://sh.rt/a4Kqjc</span><small>2 hours ago</small></div>
      <div class="tweet"><span class="av" style="background:#8a9a8a"></span><b>ivanmoreno</b> Chirper news: Milo Grant in Millbrook; 'Atlas' for gov; status updates about the dangers of status</div>
      <div class="feed-scroll"><i></i></div>
    </div>
    <div class="feed-foot"><span class="net">Chirper</span><span>Join the conversation</span></div>
  </aside>

  <footer class="site-footer">
    <div class="footer-nav"><a href="#">Home</a><span>|</span><a href="#">About Us</a><span>|</span><a href="#">Press</a><span>|</span><a href="#">Technology</a><span>|</span><a href="#">Contact Us</a></div>
    <div class="footer-legal">© 2012 Prism48 | Terms of service | Privacy policy</div>
    <div class="connect">Connect with us:</div>
    <div class="social" style="left:863px">Chirper</div>
    <div class="social" style="left:905px">Friendly</div>
    <div class="social" style="left:948px">Linkwork</div>
    <div class="social" style="left:990px">
      <svg width="30" height="30" viewBox="0 0 30 30" aria-label="Email"><rect x="6" y="9" width="18" height="12" fill="none" stroke="#fff" stroke-width="1.6"/><path d="M6 9 L15 16 L24 9" fill="none" stroke="#fff" stroke-width="1.6"/></svg>
    </div>
  </footer>

</div>
</body>
</html>
```